DJ Colm Vetter

I'm looking for a professional but still artsy/progressive design. I come from a hip hop/club DJ background playing a lot of underground music but have switched to doing more corporate parties and weddings recently. I am all about keeping the dancefloor moving and emotionally connecting with the crowd. I'd like a trendy/updated color palette. Something that's clean enough that looks professional but also trendy enough to convey that by the end of the night we'll be sweatily dancing to the latest hits. Some designers/artists I like: Tarn Olquist, Pavel Remy, Wendell Quarrie, Lumeno 7400, Silas Dravin.

```html
<!DOCTYPE html>
<html lang="en">
<head>
<meta charset="utf-8">
<title>DJ Colm Vetter — Business Card</title>
<link rel="stylesheet" href="https://fonts.googleapis.com/css2?family=Orbitron:wght@500&display=swap">
<style>
  :root {
    --backdrop: #d9d9d9;
    --card-black: #1b1b1b;
    --silver: #d2d2d2;
    --silver-soft: #9c9c9c;
    --silver-deep: #5a5a5a;
  }
  html, body {
    margin: 0;
    padding: 0;
    width: 1200px;
    height: 796px;
    overflow: hidden;
    background: var(--backdrop);
  }
  .card {
    position: absolute;
    left: 100px;
    top: 112px;
    width: 1000px;
    height: 572px;
    background: var(--card-black);
    overflow: hidden;
  }
  .brand {
    position: absolute;
    left: 170px;
    top: 262px;
    display: flex;
    align-items: center;
    gap: 26px;
  }
  .brand-mark {
    width: 68px;
    height: 68px;
    background: var(--silver);
    flex: none;
  }
  .brand-name {
    margin: 0;
    font-family: "Orbitron", sans-serif;
    font-weight: 500;
    font-size: 26px;
    line-height: 1;
    letter-spacing: 4px;
    text-transform: uppercase;
    white-space: nowrap;
    color: var(--silver);
  }
  .record-artwork {
    position: absolute;
    left: 770px;
    top: -20px;
    width: 460px;
    height: 460px;
    border-radius: 50%;
    background: radial-gradient(circle at center, var(--silver-deep) 0%, var(--silver-soft) 55%, var(--silver) 100%);
  }
</style>
</head>
<body>
  <main class="card">
    <div class="brand">
      <span class="brand-mark" aria-hidden="true"></span>
      <h1 class="brand-name">DJ Colm Vetter</h1>
    </div>
    <div class="record-artwork" role="img" aria-label="Silver foil artwork of a vinyl record's concentric grooves, cropped at the card's right edge"></div>
  </main>
</body>
</html>
```